Creative, Colorful, Dynamic Infographic for Global Non-Profit

We are a global arts and education non-profit in need of an infographic that illustrates four key skills embedded in our work: Curiosity, Listening, Imagination, Postive Action.
We work primarily with educators, students, and artists who use the power of personal stories to build community and connection and to bridge divides.
Our new brand guidelines, logos, and fonts are here: https://stylevault.example/lumen-circle
I've attached a mock-up of the graphic and the required text. (Note the attached design was created by a staff person, your final design does not need to be the same. The color scheme and text of the final design should match the brand guidelines above.)
The graphic will be used for both web and print media and should include the purple Lumen Circle logo (also attached).
Ideally the final design will delight audiences and spark interest in our work.

```html
<!DOCTYPE html>
<html lang="en">
<head>
<meta charset="utf-8">
<title>Lumen Circle – Four Skills</title>
<link rel="stylesheet" href="https://fonts.googleapis.com/css2?family=Montserrat:wght@500;600&display=swap">
<style>
  :root {
    --page: #efefef;
    --paper: #ffffff;
    --ink: #1d1d1d;
    --curiosity: #e5c845;
    --listening: #f29555;
    --imagination: #4db88c;
    --action: #ee4143;
    --brand-purple: #663399;
    --tint-curiosity: #faf4dd;
    --tint-listening: #fde9de;
    --tint-imagination: #dff2ea;
    --tint-action: #fbdde0;
  }
  html, body {
    margin: 0;
    width: 1200px;
    height: 1200px;
    overflow: hidden;
    background: var(--page);
  }
  .infographic {
    position: absolute;
    left: 0;
    top: 175px;
    width: 1200px;
    height: 849px;
    background: var(--paper);
  }
  .infographic svg { display: block; }
  text { font-family: "Montserrat", Arial, sans-serif; }
  .skill-title { font-size: 36px; font-weight: 600; letter-spacing: 1px; }
  .skill-body, .link-note { font-size: 23px; font-weight: 500; fill: var(--ink); letter-spacing: 0.6px; }
  .brand-name { font-size: 30px; font-weight: 600; fill: var(--brand-purple); }
  .bracket { fill: none; stroke-width: 5; }
  .bracket-end { fill: var(--paper); stroke-width: 4; }
  .arrow { stroke: var(--paper); stroke-width: 3; stroke-linejoin: miter; }
</style>
</head>
<body>
<main class="infographic">
<svg width="1200" height="849" viewBox="0 0 1728 1222" xmlns="http://www.w3.org/2000/svg">
  <defs>
    <linearGradient id="axis-fade-top" x1="0" y1="0" x2="0" y2="1">
      <stop offset="0" stop-color="#999" stop-opacity="0"/>
      <stop offset="1" stop-color="#777"/>
    </linearGradient>
    <linearGradient id="axis-fade-bottom" x1="0" y1="0" x2="0" y2="1">
      <stop offset="0" stop-color="#777"/>
      <stop offset="1" stop-color="#999" stop-opacity="0"/>
    </linearGradient>
    <filter id="hub-shadow" x="-20%" y="-20%" width="140%" height="140%">
      <feDropShadow dx="3" dy="4" stdDeviation="5" flood-color="#000" flood-opacity="0.3"/>
    </filter>
    <path id="cycle-arrow" d="M0,-150 L0,-240 C-130,-228 -178,-115 -172,-8 L-200,-8 L-166,36 L-133,-8 L-150,-8 A150,150 0 0 1 0,-150 Z"/>
  </defs>

  <!-- Side brackets -->
  <path class="bracket" stroke="var(--curiosity)" d="M298,233 C220,360 185,470 180,589 L65,589"/>
  <circle class="bracket-end" stroke="var(--curiosity)" cx="306" cy="221" r="11"/>
  <path class="bracket" stroke="var(--listening)" d="M65,674 L180,674 C185,793 220,904 298,1015"/>
  <circle class="bracket-end" stroke="var(--listening)" cx="306" cy="1025" r="11"/>
  <path class="bracket" stroke="var(--action)" d="M1434,233 C1512,360 1547,470 1552,589 L1663,589"/>
  <circle class="bracket-end" stroke="var(--action)" cx="1426" cy="221" r="11"/>
  <path class="bracket" stroke="var(--imagination)" d="M1663,674 L1552,674 C1547,793 1512,904 1434,1015"/>
  <circle class="bracket-end" stroke="var(--imagination)" cx="1426" cy="1025" r="11"/>

  <!-- Link notes -->
  <rect x="638" y="177" width="454" height="77" fill="var(--tint-action)"/>
  <text class="link-note" x="865" y="209" text-anchor="middle">Your positive actions inspires</text>
  <text class="link-note" x="865" y="237" text-anchor="middle">curiosity about what’s possible.</text>

  <rect x="218" y="584" width="366" height="76" fill="var(--tint-curiosity)"/>
  <text class="link-note" x="556" y="614" text-anchor="end">Your curiosity motivates</text>
  <text class="link-note" x="556" y="643" text-anchor="end">you to listen.</text>

  <rect x="1134" y="584" width="366" height="76" fill="var(--tint-imagination)"/>
  <text class="link-note" x="1161" y="614">Your imagination sparks</text>
  <text class="link-note" x="1161" y="643">positive action.</text>

  <rect x="638" y="1002" width="454" height="76" fill="var(--tint-listening)"/>
  <text class="link-note" x="865" y="1035" text-anchor="middle">Your listening lets you take</text>
  <text class="link-note" x="865" y="1063" text-anchor="middle">in new information.</text>

  <!-- Skills -->
  <text class="skill-title" x="584" y="366" text-anchor="end" fill="var(--curiosity)">CURIOSITY</text>
  <text class="skill-body" x="584" y="403" text-anchor="end">Learn from another’s</text>
  <text class="skill-body" x="584" y="432" text-anchor="end">knowledge and experience.</text>

  <text class="skill-title" x="1129" y="366" fill="var(--action)">POSITIVE ACTION</text>
  <text class="skill-body" x="1131" y="403">Show your words and</text>
  <text class="skill-body" x="1131" y="432">actions matter.</text>

  <text class="skill-title" x="586" y="825" text-anchor="end" fill="var(--listening)">LISTENING</text>
  <text class="skill-body" x="584" y="858" text-anchor="end">Seek to understand</text>
  <text class="skill-body" x="584" y="887" text-anchor="end">before speaking.</text>

  <text class="skill-title" x="1129" y="825" fill="var(--imagination)">IMAGINATION</text>
  <text class="skill-body" x="1131" y="858">Consider possibilities</text>
  <text class="skill-body" x="1131" y="887">beyond what you know.</text>

  <!-- Cycle wheel -->
  <g class="cycle" transform="translate(861,615)">
    <rect x="-1.5" y="-310" width="3" height="72" fill="url(#axis-fade-top)"/>
    <rect x="-1.5" y="240" width="3" height="82" fill="url(#axis-fade-bottom)"/>
    <use href="#cycle-arrow" class="arrow" fill="var(--curiosity)"/>
    <use href="#cycle-arrow" class="arrow" fill="var(--action)" transform="rotate(90)"/>
    <use href="#cycle-arrow" class="arrow" fill="var(--imagination)" transform="rotate(180)"/>
    <use href="#cycle-arrow" class="arrow" fill="var(--listening)" transform="rotate(270)"/>
    <circle r="148" fill="var(--paper)" filter="url(#hub-shadow)"/>
    <text class="brand-name" y="-6" text-anchor="middle">Lumen</text>
    <text class="brand-name" y="30" text-anchor="middle">Circle</text>
  </g>
</svg>
</main>
</body>
</html>
```